Business card for marketing analytics company

Need a business card for new company. I have a logo already that I want to be built into the card and should use those colours

Company is called steered by tallies
Design must bring steered by tallies to life not be a card that could be for anyone with a logo put on it.

Like the front to be fairly clean and uncluttered bringing the logo out with a suitable design on the back of the card.

The logo represents a compass and business growth so those themes along with numbers, analytics , data are appropriate.
I'm often working with creative industries so also needs to reflect the creative side of analytics rather than be very corporate looking.

Target Market(s)

Ad agency, media agency, consumer goods clients

Industry/Entity Type

Market Research

Contact Information for Business Card

Needs to include name, title, email and phone number

Colors
f78f20
f68d4d
ec1f27

Requirements
Must have
• Must bring steered by tallies to life not be a card that could be for anyone with a logo put on it.
• Logo, Correct colours
• Like a design on the back that relates to company name
• Designs for both sides
Should not have
• Please do not just submit logo and a coloured card.
• It needs to have a design element to it
• No black background
• No clear cards - needs front & back

```html
<!DOCTYPE html>
<html lang="en">
<head>
<meta charset="utf-8">
<title>Steered by Tallies – Business Card</title>
<link rel="stylesheet" href="https://fonts.googleapis.com/css2?family=Open+Sans:wght@400;600;700&display=swap">
<style>
  :root {
    --page-bg: #e9e9ea;
    --brand-red: #ec1f27;
    --mark-red: #c8242b;
    --card-red: #b01e24;
    --card-red-light: #c4252b;
    --brand-orange: #f78f20;
    --ink: #4a5258;
    --ink-soft: #5b6268;
    --paper: #ffffff;
  }
  * { box-sizing: border-box; margin: 0; padding: 0; }
  html, body {
    width: 1200px; height: 1000px; overflow: hidden;
    background: var(--page-bg);
    font-family: "Open Sans", Arial, sans-serif;
  }
  .canvas { position: relative; width: 1200px; height: 1000px; }

  .card {
    position: absolute; left: 240px; width: 720px; height: 411px;
    border-radius: 22px; overflow: hidden;
    box-shadow: 0 10px 28px rgba(0,0,0,0.18);
  }

  /* Front side */
  .card--front {
    top: 60px;
    background: linear-gradient(100deg, var(--card-red-light) 0%, var(--card-red) 55%, var(--card-red) 100%);
  }
  .front-brand {
    position: absolute; inset: 0;
    display: flex; align-items: center; justify-content: center; gap: 26px;
  }
  .front-brand__dot {
    width: 84px; height: 84px; border-radius: 50%;
    background: var(--paper);
  }
  .front-brand__name {
    color: var(--paper); font-weight: 600; font-size: 44px; line-height: 1.05;
  }
  .front-brand__name span { display: block; padding-left: 60px; }

  /* Back side */
  .card--back { top: 530px; background: var(--paper); }
  .card--back::after {
    content: ""; position: absolute; left: 0; right: 0; bottom: 0; height: 16px;
    background: var(--brand-red);
  }
  .back-brand {
    position: absolute; left: 46px; top: 30px;
    color: var(--brand-orange); font-weight: 600; font-size: 52px; line-height: 0.98;
  }
  .back-brand span { display: block; padding-left: 60px; }

  .holder { position: absolute; left: 46px; top: 160px; }
  .holder__tab {
    position: absolute; left: -46px; top: 4px; width: 10px; height: 28px;
    background: var(--brand-red); border-radius: 0 4px 4px 0;
  }
  .holder__name {
    color: var(--ink); font-weight: 700; font-size: 28px; letter-spacing: 0.5px;
  }
  .holder__title {
    color: var(--brand-red); font-weight: 600; font-size: 17px; margin-top: -2px;
  }

  .address {
    position: absolute; left: 46px; top: 236px;
    color: var(--ink-soft); font-size: 17px; line-height: 1.3;
  }

  .contacts {
    position: absolute; left: 46px; top: 296px; list-style: none;
    color: var(--ink); font-size: 18px; line-height: 1.5;
  }
  .contacts li { display: flex; align-items: center; gap: 14px; }
  .contacts svg { width: 14px; height: 14px; fill: var(--brand-red); flex: none; }
  .contacts .accent { color: var(--brand-red); }

  .brand-seal {
    position: absolute; right: 80px; bottom: 50px;
    width: 230px; height: 230px; border-radius: 50%;
    border: 4px solid var(--mark-red);
    display: flex; align-items: center; justify-content: center; text-align: center;
    color: var(--mark-red); font-weight: 600; font-size: 26px; line-height: 1.1;
  }
</style>
</head>
<body>
<main class="canvas">

  <section class="card card--front" aria-label="Card front">
    <div class="front-brand">
      <div class="front-brand__dot"></div>
      <p class="front-brand__name">Steered by<span>Tallies</span></p>
    </div>
  </section>

  <section class="card card--back" aria-label="Card back">
    <p class="back-brand">Steered by<span>Tallies</span></p>

    <div class="holder">
      <div class="holder__tab"></div>
      <h1 class="holder__name">DANA WHITFIELD</h1>
      <p class="holder__title">Ceo/Founer</p>
    </div>

    <p class="address">Your Street Address,<br>Singapore, 1234</p>

    <ul class="contacts">
      <li>
        <svg viewBox="0 0 16 16" aria-hidden="true"><path d="M3.6 1.2l2.3 2.6-1.3 1.7c.9 2 2.4 3.5 4.3 4.4l1.7-1.3 2.6 2.3-1.2 2.2C7 12.8 3.2 9 1.4 3.4z"/></svg>
        <span>+000 123 456 789</span>
      </li>
      <li>
        <svg viewBox="0 0 16 16" aria-hidden="true"><path d="M1 3h14v10H1z M2 4l6 5 6-5" stroke="#fff" stroke-width="1"/></svg>
        <span>yourname@email.com</span>
      </li>
      <li>
        <svg viewBox="0 0 16 16" aria-hidden="true"><circle cx="8" cy="8" r="7"/><path d="M1 8h14M8 1v14M3 4h10M3 12h10" stroke="#fff" stroke-width="0.9" fill="none"/></svg>
        <span>www.<span class="accent">websitename</span>.com</span>
      </li>
    </ul>

    <p class="brand-seal">Steered by<br>Tallies</p>
  </section>

</main>
</body>
</html>
```